Email Signature

Hello,

We need an editable file so that when new staff start or someone is promoted we can easily edit this file.

The previous designer has not kept the email signatures uniform they should all be as per Dale Fenwick signature.

I also need the Omar Qadri changes as below -
Senior Mechanical Engineer
Email should be omar.qadri@tovek.com.au

You can see the Glen Harper file is different I need this the same as Dale Fenwick format but with details changed.

Also need a new one with details as per below -
Kevin Doyle
Commercial Manager
0417 263 519
kevin.doyle@tovek.com.au
www.tovek.com.au

```html
<!DOCTYPE html>
<html lang="en">
<head>
<meta charset="utf-8">
<title>Tovek Email Signatures</title>
<link rel="stylesheet" href="https://fonts.googleapis.com/css2?family=Hind:wght@400;500&family=Roboto:wght@700&family=Lexend:wght@700&display=swap">
<style>
  :root {
    --backdrop: #808080;
    --headline: #31c4f3;
    --brand-blue: #33c4f2;
    --name-blue: #2b85d6;
    --icon-blue: #2a8fdc;
    --band-green: #8dc63f;
    --ink: #222;
    --card: #fff;
  }
  * { margin: 0; padding: 0; box-sizing: border-box; }
  html, body { width: 785px; height: 1200px; overflow: hidden; }
  body { background: var(--backdrop); position: relative; font-family: "Hind", sans-serif; }
  .headline {
    position: absolute; left: 0; top: 42px; width: 785px; text-align: center;
    font-family: Arial, "Helvetica Neue", sans-serif; font-weight: 700;
    font-size: 94px; color: var(--headline); letter-spacing: 1px; line-height: 1;
  }
  .signature {
    position: absolute; left: 92px; width: 600px; height: 200px;
    background: var(--card); box-shadow: 0 6px 12px rgba(0,0,0,.35);
  }
  .details { position: absolute; left: 18px; top: 20px; }
  .name {
    font-family: "Roboto", sans-serif; font-weight: 700; font-size: 26px;
    color: var(--name-blue); line-height: 1.05;
  }
  .role { font-size: 15px; color: var(--ink); line-height: 1.4; margin-top: 2px; }
  .contacts { list-style: none; margin-top: 12px; }
  .contacts li {
    display: flex; align-items: center; gap: 8px;
    font-size: 15.5px; color: var(--ink); height: 25px;
  }
  .contact-icon { width: 18px; height: 18px; flex: none; }
  .wordmark {
    position: absolute; left: 262px; top: 40px; width: 320px; text-align: center;
    font-family: "Lexend", sans-serif; font-weight: 700; font-size: 92px;
    line-height: 1; color: var(--brand-blue); letter-spacing: 2px;
  }
  .band { position: absolute; left: 0; bottom: 0; width: 600px; height: 22px; }
  .band-bg { position: absolute; left: 0; top: 0; width: 600px; height: 22px; }
  .band-text {
    position: absolute; top: 0; height: 22px; display: flex; align-items: center; gap: 4px;
    font-family: "Lexend", sans-serif; font-weight: 700; font-size: 13px; color: #fff;
    white-space: nowrap;
  }
  .pin-icon { width: 9px; height: 12px; flex: none; }
  .address { left: 12px; }
  .hotline { left: 408px; letter-spacing: 1.5px; }
  .social { display: flex; gap: 3px; margin-left: 6px; }
  .social span { width: 11px; height: 11px; border-radius: 50%; background: var(--icon-blue); border: 1px solid #fff; }
</style>
</head>
<body>
<svg width="0" height="0" style="position:absolute">
  <defs>
    <linearGradient id="bandBlue" x1="0" y1="0" x2="0" y2="1">
      <stop offset="0" stop-color="#3cb6ef"/><stop offset="1" stop-color="#1e7fcf"/>
    </linearGradient>
    <symbol id="icon-phone" viewBox="0 0 20 20">
      <circle cx="10" cy="10" r="10" fill="#2a8fdc"/>
      <path d="M7 5.5l1.6 2.2-1 1.2a7 7 0 003.5 3.5l1.2-1 2.2 1.6-.9 1.7c-3.8.2-8-4-7.8-7.8z" fill="#fff"/>
    </symbol>
    <symbol id="icon-mail" viewBox="0 0 20 20">
      <circle cx="10" cy="10" r="10" fill="#2a8fdc"/>
      <rect x="5" y="6.5" width="10" height="7" rx="1" fill="#fff"/>
      <path d="M5.5 7l4.5 3.5L14.5 7" fill="none" stroke="#2a8fdc" stroke-width="1.2"/>
    </symbol>
    <symbol id="icon-web" viewBox="0 0 20 20">
      <circle cx="10" cy="10" r="10" fill="#2a8fdc"/>
      <circle cx="10" cy="10" r="5.5" fill="none" stroke="#fff" stroke-width="1.3"/>
      <path d="M4.5 10h11M10 4.5c-2.5 3-2.5 8 0 11M10 4.5c2.5 3 2.5 8 0 11" fill="none" stroke="#fff" stroke-width="1"/>
    </symbol>
    <symbol id="icon-pin" viewBox="0 0 10 14">
      <path d="M5 0a5 5 0 00-5 5c0 3.5 5 9 5 9s5-5.5 5-9a5 5 0 00-5-5zm0 7a2 2 0 110-4 2 2 0 010 4z" fill="#fff"/>
    </symbol>
    <symbol id="band-shape" viewBox="0 0 600 22" preserveAspectRatio="none">
      <polygon points="0,0 392,0 384,22 0,22" fill="url(#bandBlue)"/>
      <polygon points="396,0 600,0 600,22 388,22" fill="#8dc63f"/>
    </symbol>
  </defs>
</svg>

<h1 class="headline">Editable file</h1>

<section class="signature" style="top:192px">
  <div class="details">
    <p class="name">Kevin Doyle</p>
    <p class="role">Commercial Manager</p>
    <ul class="contacts">
      <li><svg class="contact-icon"><use href="#icon-phone"/></svg>0417 263 519</li>
      <li><svg class="contact-icon"><use href="#icon-mail"/></svg>kevin.doyle@tovek.com.au</li>
      <li><svg class="contact-icon"><use href="#icon-web"/></svg>www.tovek.com.au</li>
    </ul>
  </div>
  <p class="wordmark">TOVEK</p>
  <div class="band">
    <svg class="band-bg"><use href="#band-shape"/></svg>
    <p class="band-text address"><svg class="pin-icon"><use href="#icon-pin"/></svg>14/ 220 Kessel Road, Brandon QLD 4051</p>
    <p class="band-text hotline">1300 452 610<span class="social"><span></span><span></span><span></span></span></p>
  </div>
</section>

<section class="signature" style="top:423px">
  <div class="details" style="top:14px">
    <p class="name">Omar Qadri</p>
    <p class="role">Senior Mechanical Engineer<br>RPEQ, NER, MIEAust</p>
    <ul class="contacts" style="margin-top:6px">
      <li><svg class="contact-icon"><use href="#icon-phone"/></svg>0417 263 519</li>
      <li><svg class="contact-icon"><use href="#icon-mail"/></svg>omar.qadri@tovek.com.au</li>
      <li><svg class="contact-icon"><use href="#icon-web"/></svg>www.tovek.com.au</li>
    </ul>
  </div>
  <p class="wordmark">TOVEK</p>
  <div class="band">
    <svg class="band-bg"><use href="#band-shape"/></svg>
    <p class="band-text address"><svg class="pin-icon"><use href="#icon-pin"/></svg>14/ 220 Kessel Road, Brandon QLD 4051</p>
    <p class="band-text hotline">1300 452 610<span class="social"><span></span><span></span><span></span></span></p>
  </div>
</section>

<section class="signature" style="top:655px">
  <div class="details">
    <p class="name">Glen Harper</p>
    <p class="role">Director</p>
    <ul class="contacts">
      <li><svg class="contact-icon"><use href="#icon-phone"/></svg>0438 915 206</li>
      <li><svg class="contact-icon"><use href="#icon-mail"/></svg>glen.harper@tovek.com.au</li>
      <li><svg class="contact-icon"><use href="#icon-web"/></svg>www.tovek.com.au</li>
    </ul>
  </div>
  <p class="wordmark">TOVEK</p>
  <div class="band">
    <svg class="band-bg"><use href="#band-shape"/></svg>
    <p class="band-text address"><svg class="pin-icon"><use href="#icon-pin"/></svg>14/ 220 Kessel Road, Brandon QLD 4051</p>
    <p class="band-text hotline">1300 452 610<span class="social"><span></span><span></span><span></span></span></p>
  </div>
</section>

<section class="signature" style="top:887px">
  <div class="details">
    <p class="name">Dale Fenwick</p>
    <p class="role">Site Project Manager</p>
    <ul class="contacts">
      <li><svg class="contact-icon"><use href="#icon-phone"/></svg>0455 318 742</li>
      <li><svg class="contact-icon"><use href="#icon-mail"/></svg>dale.fenwick@tovek.com.au</li>
      <li><svg class="contact-icon"><use href="#icon-web"/></svg>www.tovek.com.au</li>
    </ul>
  </div>
  <p class="wordmark">TOVEK</p>
  <div class="band">
    <svg class="band-bg"><use href="#band-shape"/></svg>
    <p class="band-text address"><svg class="pin-icon"><use href="#icon-pin"/></svg>14/ 220 Kessel Road, Brandon QLD 4051</p>
    <p class="band-text hotline">1300 452 610<span class="social"><span></span><span></span><span></span></span></p>
  </div>
</section>
</body>
</html>
```